Income Tax Flyer - Updates Needed

Just need to update this flyer design and give it a new look. We would like to keep all the same wording but make it stand out a little more. Our selling point is the "Same Day Tax Advance up to $6,000"

Lending, Small Loans, Tax Services, Title Loans, Personal Loans

```html
<!DOCTYPE html>
<html lang="en">
<head>
<meta charset="utf-8">
<title>Same Day Tax Advance Flyer</title>
<link href="https://fonts.googleapis.com/css2?family=Anton&family=Montserrat:wght@800;900&family=Poppins:wght@300;400;600;700;800&display=swap" rel="stylesheet">
<style>
  :root{
    --page:#f1f1f1;
    --ink:#1b1b1b;
    --red:#c41e26;
    --green:#0b7a3b;
    --green-dark:#075a2b;
    --white:#ffffff;
    --shadow:rgba(0,0,0,.18);
  }
  *{margin:0;padding:0;box-sizing:border-box}
  html,body{width:679px;height:1200px;overflow:hidden;background:var(--page)}
  .flyer{
    position:absolute;left:10px;top:94px;width:660px;height:1012px;overflow:hidden;
    background:radial-gradient(circle at 62% 40%,#ffffff 0%,#f3f3f3 45%,#e6e6e6 100%);
    box-shadow:0 4px 14px var(--shadow);
    font-family:'Poppins',sans-serif;
  }
  .brand{position:absolute;left:130px;width:200px;top:62px;text-align:center;color:var(--green);font-weight:600}
  .brand-name{display:block;font-size:36px;line-height:1;white-space:nowrap}
  .brand-sub{display:block;font-size:10px;letter-spacing:4px;margin-top:8px;white-space:nowrap}
  .brand-dot{display:inline-block;width:12px;height:12px;border-radius:50%;background:var(--green);margin-right:8px;vertical-align:middle}

  .photo{position:absolute;left:407px;top:223px;width:253px;height:349px;
    background:linear-gradient(180deg,#e9d6c0 0%,#cfae8c 45%,#3e5b86 80%,#2d4468 100%);border-radius:120px 120px 8px 8px}
  .bill{position:absolute;width:44px;height:22px;background:linear-gradient(135deg,#c9d8bf,#93ab86);border-radius:2px}

  .same-day{position:absolute;left:44px;top:150px;font-family:'Montserrat',sans-serif;font-weight:900;font-size:58px;letter-spacing:4px;line-height:1;color:var(--ink);white-space:nowrap}
  .tax{position:absolute;left:40px;top:196px;font-family:'Montserrat',sans-serif;font-weight:900;font-size:172px;line-height:1;color:var(--red);letter-spacing:-4px;white-space:nowrap}
  .advance{position:absolute;left:46px;top:340px;font-family:'Montserrat',sans-serif;font-size:43px;line-height:1;color:var(--ink);white-space:nowrap}
  .advance b{font-weight:900}
  .advance span{font-family:'Poppins',sans-serif;font-weight:400}
  .amount{
    position:absolute;left:44px;top:386px;font-family:'Anton',sans-serif;color:var(--green);
    font-size:150px;line-height:1;transform:scaleX(.96);transform-origin:left top;white-space:nowrap;
    text-shadow:2px 2px 0 var(--green-dark),4px 4px 0 var(--green-dark),6px 6px 8px rgba(0,0,0,.25);
  }
  .amount sup{font-size:74px;vertical-align:top;position:relative;top:2px}

  .band{position:absolute;left:0;top:578px;width:660px;height:434px}
  .band svg{position:absolute;left:0;top:0}
  .tagline{position:absolute;left:0;width:100%;top:626px;text-align:center;color:var(--white);font-size:32px;font-weight:300;line-height:1.15}
  .tagline strong{display:block;font-weight:800;font-size:32px}
  .feature{position:absolute;top:740px;width:174px;height:139px;background:var(--green);border:2px solid var(--white);border-radius:14px;
    color:var(--white);font-weight:700;font-size:19px;line-height:1.2;text-align:center;display:flex;align-items:center;justify-content:center;padding-top:30px}
  .feature-icon{position:absolute;left:50%;top:-38px;margin-left:-33px;width:66px;height:66px;border-radius:50%;background:var(--white);border:3px solid var(--red);display:flex;align-items:center;justify-content:center}
  .contact{position:absolute;left:56px;top:906px;color:var(--white)}
  .contact-label{font-size:22px;font-weight:400;letter-spacing:.5px;line-height:1}
  .contact-phone{font-size:27px;font-weight:700;margin-top:6px;display:flex;align-items:center;gap:6px}
  .divider{position:absolute;left:330px;top:906px;width:2px;height:58px;background:var(--white)}
  .location{position:absolute;left:350px;top:906px;color:var(--white);font-size:15.5px;line-height:1.25;display:flex;gap:8px}
  .location b{font-weight:800}
</style>
</head>
<body>
<main class="flyer">
  <div class="brand">
    <span class="brand-name"><span class="brand-dot"></span>Ledgerline</span>
    <span class="brand-sub">FINANCIAL GROUP</span>
  </div>

  <div class="bill" role="img" aria-label="Falling banknote" style="left:520px;top:40px;transform:rotate(28deg)"></div>
  <div class="bill" role="img" aria-label="Falling banknote" style="left:460px;top:120px;transform:rotate(60deg)"></div>
  <div class="bill" role="img" aria-label="Falling banknote" style="left:580px;top:150px;transform:rotate(25deg)"></div>
  <div class="bill" role="img" aria-label="Falling banknote" style="left:430px;top:250px;transform:rotate(40deg)"></div>

  <div class="photo" role="img" aria-label="Photo of a smiling man sitting cross-legged holding a fan of cash and pointing at the offer"></div>

  <div class="same-day">SAME DAY</div>
  <div class="tax">TAX</div>
  <div class="advance"><b>ADVANCE</b> <span>UP TO</span></div>
  <div class="amount"><sup>$</sup>6,000</div>

  <div class="band">
    <svg width="660" height="434" viewBox="0 0 660 434" aria-hidden="true">
      <path d="M0 18 Q90 -6 180 16 Q260 -8 330 16 Q400 -8 480 16 Q570 -6 660 18 L660 434 L0 434 Z" fill="var(--red)"/>
    </svg>
  </div>

  <p class="tagline">File your taxes and apply for an<strong>EASY ADVANCE!</strong></p>

  <div class="feature" style="left:54px">
    <span class="feature-icon">
      <svg width="40" height="40" viewBox="0 0 40 40" fill="none" stroke="#222" stroke-width="2.2"><circle cx="20" cy="20" r="16"/><path d="M20 10v10l7 5"/></svg>
    </span>Available<br>In 24 Hours<br>or Less
  </div>
  <div class="feature" style="left:244px">
    <span class="feature-icon">
      <svg width="40" height="40" viewBox="0 0 40 40" fill="none" stroke="#222" stroke-width="2.2"><rect x="7" y="9" width="26" height="15" rx="2"/><circle cx="20" cy="16.5" r="3.5"/><path d="M5 30h10l5 3 10-4"/></svg>
    </span>Choose<br>Your Loan<br>Amount
  </div>
  <div class="feature" style="left:435px">
    <span class="feature-icon">
      <svg width="40" height="40" viewBox="0 0 40 40" fill="none" stroke="#222" stroke-width="2.2"><circle cx="22" cy="22" r="12"/><path d="M22 15v7l4 3M19 6h6M4 18h6M2 24h7M5 30h6"/></svg>
    </span>Quick<br>and Easy
  </div>

  <div class="contact">
    <div class="contact-label">CONTACT US TODAY!</div>
    <div class="contact-phone">
      <svg width="24" height="24" viewBox="0 0 24 24" fill="#21a84a"><path d="M6.6 10.8a15 15 0 0 0 6.6 6.6l2.2-2.2a1 1 0 0 1 1-.25 11 11 0 0 0 3.6.6 1 1 0 0 1 1 1V20a1 1 0 0 1-1 1A17 17 0 0 1 3 4a1 1 0 0 1 1-1h3.5a1 1 0 0 1 1 1 11 11 0 0 0 .6 3.6 1 1 0 0 1-.25 1z"/></svg>
      (555) 014-2290
    </div>
  </div>
  <div class="divider"></div>
  <div class="location">
    <svg width="18" height="24" viewBox="0 0 18 24" fill="#21a84a"><path d="M9 0a9 9 0 0 0-9 9c0 6.8 9 15 9 15s9-8.2 9-15a9 9 0 0 0-9-9zm0 12.5A3.5 3.5 0 1 1 9 5.5a3.5 3.5 0 0 1 0 7z"/></svg>
    <div><b>FAIRVIEW – ELM STREET</b><br>2150-3 ELM STREET AVE<br>FAIRVIEW, TEXAS 78000</div>
  </div>
</main>
</body>
</html>
```